Birthday Calendar: Dec 1 - Nov 30

This calendar should have three parts. First the center should contain an annual calendar beginning December 1, 2019 and going through November 30, 2020. I'm picturing the months and date numbers - no need for individual boxes for each day. Second, above the calendar should be blank space (intended for people to write words of advise and love). Third, beneath the calendar space will be several statements about the year (i.e. "If you have client meetings four times a month, you'll meet with 36 clients." "If you kiss your kids only once each day, that's 1,460 kisses.") I don't have an exact overall size of the calendar in mind, but definitely know it will need to be bigger than 8.5"x11"

Target Market(s)

Wife - Her birthday is November 30, so this is a calendar to mark the time from one birthday to the next.

Font styles to use
Serif

Colors

Designer to choose colors to be used in the design.

Requirements
Must have
• The three different sections listed in the description. There will be 12 people handwriting simple phrases of advise (for how to have the best year) at the top, so there should be enough room for that. At the top it should say "These are the Days"
• I will provide the complete set of statements that will appear at the bottom of the calendar. There will be 10 (or less) statements total, sort of like the ones provided in the description. Let me know when you want those statements.

```html
<!DOCTYPE html>
<html lang="en">
<head>
<meta charset="utf-8">
<title>These are the Days — Birthday Calendar</title>
<link rel="stylesheet" href="https://fonts.googleapis.com/css2?family=Pinyon+Script&family=Noto+Serif:wght@700&family=Roboto+Condensed:wght@700&display=swap">
<style>
  :root {
    --wine: #9a1539;
    --title-red: #9e1a40;
    --card-green: #dde6bf;
    --card-blue: #d3eae8;
    --ink: #1e1e24;
    --navy: #1f2a48;
    --paper: #ffffff;
  }
  * { box-sizing: border-box; margin: 0; padding: 0; }
  html, body { width: 776px; height: 1200px; overflow: hidden; }
  body {
    position: relative;
    background: linear-gradient(to bottom, var(--paper) 0, var(--paper) 758px, #d9a7b3 830px, #b24a64 900px, var(--wine) 966px, var(--wine) 1200px);
    font-family: "Noto Serif", Georgia, serif;
  }
  .title {
    position: absolute;
    font-family: "Pinyon Script", cursive;
    color: var(--title-red);
    font-weight: 400;
    font-size: 96px;
    line-height: 1;
    white-space: nowrap;
  }
  .title-line-1 { left: 54px; top: 48px; }
  .title-line-2 { left: 326px; top: 130px; }

  .advice-space { position: absolute; left: 54px; top: 240px; width: 668px; height: 260px; }

  .year-grid {
    position: absolute;
    left: 71px;
    top: 518px;
    width: 634px;
    display: grid;
    grid-template-columns: repeat(4, 158.5px);
    row-gap: 15px;
  }
  .month {
    height: 116px;
    border-radius: 4px 4px 9px 9px;
    box-shadow: 0 3px 3px rgba(0,0,0,.55);
    padding-top: 5px;
  }
  .month.green { background: var(--card-green); }
  .month.blue { background: var(--card-blue); }
  .month-name {
    text-align: center;
    color: var(--title-red);
    font-size: 11.5px;
    line-height: 14px;
    letter-spacing: .1px;
  }
  .days {
    display: grid;
    grid-template-columns: repeat(7, 22.6px);
    font-size: 11px;
    line-height: 14.2px;
    color: var(--ink);
    text-align: center;
  }
  .weekday {
    font-family: "Roboto Condensed", "Arial Narrow", sans-serif;
    color: var(--navy);
    text-decoration: underline;
    font-size: 11px;
    line-height: 13px;
    margin-bottom: 1px;
  }

  .facts {
    position: absolute;
    left: 71px;
    top: 922px;
    width: 634px;
    color: #fff;
    font-size: 12.6px;
    line-height: 22.6px;
  }
  .fact.left { text-align: left; }
  .fact.right { text-align: right; }
</style>
</head>
<body>
  <h1 class="title title-line-1">These are</h1>
  <div class="title title-line-2">the Days</div>

  <div class="advice-space" aria-label="Space for handwritten advice"></div>

  <section class="year-grid">
    <div class="month green"><div class="month-name">DECEMBER 2019</div><div class="days">
      <span class="weekday">Su</span><span class="weekday">Mo</span><span class="weekday">Tu</span><span class="weekday">We</span><span class="weekday">Th</span><span class="weekday">Fr</span><span class="weekday">Sa</span>
      <span>1</span><span>2</span><span>3</span><span>4</span><span>5</span><span>6</span><span>7</span><span>8</span><span>9</span><span>10</span><span>11</span><span>12</span><span>13</span><span>14</span><span>15</span><span>16</span><span>17</span><span>18</span><span>19</span><span>20</span><span>21</span><span>22</span><span>23</span><span>24</span><span>25</span><span>26</span><span>27</span><span>28</span><span>29</span><span>30</span><span>31</span>
    </div></div>
    <div class="month blue"><div class="month-name">JANUARY 2020</div><div class="days">
      <span class="weekday">Su</span><span class="weekday">Mo</span><span class="weekday">Tu</span><span class="weekday">We</span><span class="weekday">Th</span><span class="weekday">Fr</span><span class="weekday">Sa</span>
      <span style="grid-column-start:4">1</span><span>2</span><span>3</span><span>4</span><span>5</span><span>6</span><span>7</span><span>8</span><span>9</span><span>10</span><span>11</span><span>12</span><span>13</span><span>14</span><span>15</span><span>16</span><span>17</span><span>18</span><span>19</span><span>20</span><span>21</span><span>22</span><span>23</span><span>24</span><span>25</span><span>26</span><span>27</span><span>28</span><span>29</span><span>30</span><span>31</span>
    </div></div>
    <div class="month green"><div class="month-name">FEBRUARY 2020</div><div class="days">
      <span class="weekday">Su</span><span class="weekday">Mo</span><span class="weekday">Tu</span><span class="weekday">We</span><span class="weekday">Th</span><span class="weekday">Fr</span><span class="weekday">Sa</span>
      <span style="grid-column-start:7">1</span><span>2</span><span>3</span><span>4</span><span>5</span><span>6</span><span>7</span><span>8</span><span>9</span><span>10</span><span>11</span><span>12</span><span>13</span><span>14</span><span>15</span><span>16</span><span>17</span><span>18</span><span>19</span><span>20</span><span>21</span><span>22</span><span>23</span><span>24</span><span>25</span><span>26</span><span>27</span><span>28</span><span>29</span>
    </div></div>
    <div class="month blue"><div class="month-name">MARCH 2020</div><div class="days">
      <span class="weekday">Su</span><span class="weekday">Mo</span><span class="weekday">Tu</span><span class="weekday">We</span><span class="weekday">Th</span><span class="weekday">Fr</span><span class="weekday">Sa</span>
      <span>1</span><span>2</span><span>3</span><span>4</span><span>5</span><span>6</span><span>7</span><span>8</span><span>9</span><span>10</span><span>11</span><span>12</span><span>13</span><span>14</span><span>15</span><span>16</span><span>17</span><span>18</span><span>19</span><span>20</span><span>21</span><span>22</span><span>23</span><span>24</span><span>25</span><span>26</span><span>27</span><span>28</span><span>29</span><span>30</span><span>31</span>
    </div></div>

    <div class="month blue"><div class="month-name">APRIL 2020</div><div class="days">
      <span class="weekday">Su</span><span class="weekday">Mo</span><span class="weekday">Tu</span><span class="weekday">We</span><span class="weekday">Th</span><span class="weekday">Fr</span><span class="weekday">Sa</span>
      <span style="grid-column-start:4">1</span><span>2</span><span>3</span><span>4</span><span>5</span><span>6</span><span>7</span><span>8</span><span>9</span><span>10</span><span>11</span><span>12</span><span>13</span><span>14</span><span>15</span><span>16</span><span>17</span><span>18</span><span>19</span><span>20</span><span>21</span><span>22</span><span>23</span><span>24</span><span>25</span><span>26</span><span>27</span><span>28</span><span>29</span><span>30</span>
    </div></div>
    <div class="month green"><div class="month-name">MAY 2020</div><div class="days">
      <span class="weekday">Su</span><span class="weekday">Mo</span><span class="weekday">Tu</span><span class="weekday">We</span><span class="weekday">Th</span><span class="weekday">Fr</span><span class="weekday">Sa</span>
      <span style="grid-column-start:6">1</span><span>2</span><span>3</span><span>4</span><span>5</span><span>6</span><span>7</span><span>8</span><span>9</span><span>10</span><span>11</span><span>12</span><span>13</span><span>14</span><span>15</span><span>16</span><span>17</span><span>18</span><span>19</span><span>20</span><span>21</span><span>22</span><span>23</span><span>24</span><span>25</span><span>26</span><span>27</span><span>28</span><span>29</span><span>30</span><span>31</span>
    </div></div>
    <div class="month blue"><div class="month-name">JUNE 2020</div><div class="days">
      <span class="weekday">Su</span><span class="weekday">Mo</span><span class="weekday">Tu</span><span class="weekday">We</span><span class="weekday">Th</span><span class="weekday">Fr</span><span class="weekday">Sa</span>
      <span style="grid-column-start:2">1</span><span>2</span><span>3</span><span>4</span><span>5</span><span>6</span><span>7</span><span>8</span><span>9</span><span>10</span><span>11</span><span>12</span><span>13</span><span>14</span><span>15</span><span>16</span><span>17</span><span>18</span><span>19</span><span>20</span><span>21</span><span>22</span><span>23</span><span>24</span><span>25</span><span>26</span><span>27</span><span>28</span><span>29</span><span>30</span>
    </div></div>
    <div class="month green"><div class="month-name">JULY 2020</div><div class="days">
      <span class="weekday">Su</span><span class="weekday">Mo</span><span class="weekday">Tu</span><span class="weekday">We</span><span class="weekday">Th</span><span class="weekday">Fr</span><span class="weekday">Sa</span>
      <span style="grid-column-start:4">1</span><span>2</span><span>3</span><span>4</span><span>5</span><span>6</span><span>7</span><span>8</span><span>9</span><span>10</span><span>11</span><span>12</span><span>13</span><span>14</span><span>15</span><span>16</span><span>17</span><span>18</span><span>19</span><span>20</span><span>21</span><span>22</span><span>23</span><span>24</span><span>25</span><span>26</span><span>27</span><span>28</span><span>29</span><span>30</span><span>31</span>
    </div></div>

    <div class="month green"><div class="month-name">AUGUST 2020</div><div class="days">
      <span class="weekday">Su</span><span class="weekday">Mo</span><span class="weekday">Tu</span><span class="weekday">We</span><span class="weekday">Th</span><span class="weekday">Fr</span><span class="weekday">Sa</span>
      <span style="grid-column-start:7">1</span><span>2</span><span>3</span><span>4</span><span>5</span><span>6</span><span>7</span><span>8</span><span>9</span><span>10</span><span>11</span><span>12</span><span>13</span><span>14</span><span>15</span><span>16</span><span>17</span><span>18</span><span>19</span><span>20</span><span>21</span><span>22</span><span>23</span><span>24</span><span>25</span><span>26</span><span>27</span><span>28</span><span>29</span><span>30</span><span>31</span>
    </div></div>
    <div class="month blue"><div class="month-name">SEPTEMBER 2020</div><div class="days">
      <span class="weekday">Su</span><span class="weekday">Mo</span><span class="weekday">Tu</span><span class="weekday">We</span><span class="weekday">Th</span><span class="weekday">Fr</span><span class="weekday">Sa</span>
      <span style="grid-column-start:3">1</span><span>2</span><span>3</span><span>4</span><span>5</span><span>6</span><span>7</span><span>8</span><span>9</span><span>10</span><span>11</span><span>12</span><span>13</span><span>14</span><span>15</span><span>16</span><span>17</span><span>18</span><span>19</span><span>20</span><span>21</span><span>22</span><span>23</span><span>24</span><span>25</span><span>26</span><span>27</span><span>28</span><span>29</span><span>30</span>
    </div></div>
    <div class="month green"><div class="month-name">OCTOBER 2020</div><div class="days">
      <span class="weekday">Su</span><span class="weekday">Mo</span><span class="weekday">Tu</span><span class="weekday">We</span><span class="weekday">Th</span><span class="weekday">Fr</span><span class="weekday">Sa</span>
      <span style="grid-column-start:5">1</span><span>2</span><span>3</span><span>4</span><span>5</span><span>6</span><span>7</span><span>8</span><span>9</span><span>10</span><span>11</span><span>12</span><span>13</span><span>14</span><span>15</span><span>16</span><span>17</span><span>18</span><span>19</span><span>20</span><span>21</span><span>22</span><span>23</span><span>24</span><span>25</span><span>26</span><span>27</span><span>28</span><span>29</span><span>30</span><span>31</span>
    </div></div>
    <div class="month blue"><div class="month-name">NOVEMBER 2020</div><div class="days">
      <span class="weekday">Su</span><span class="weekday">Mo</span><span class="weekday">Tu</span><span class="weekday">We</span><span class="weekday">Th</span><span class="weekday">Fr</span><span class="weekday">Sa</span>
      <span>1</span><span>2</span><span>3</span><span>4</span><span>5</span><span>6</span><span>7</span><span>8</span><span>9</span><span>10</span><span>11</span><span>12</span><span>13</span><span>14</span><span>15</span><span>16</span><span>17</span><span>18</span><span>19</span><span>20</span><span>21</span><span>22</span><span>23</span><span>24</span><span>25</span><span>26</span><span>27</span><span>28</span><span>29</span><span>30</span>
    </div></div>
  </section>

  <section class="facts">
    <p class="fact left">If you have client meetings four times a month, you'll meet with 36 clients.</p>
    <p class="fact right">If you kiss your kids only once each day, that's 1,460 kisses.</p>
    <p class="fact left">If you have client meetings four times a month, you'll meet with 36 clients.</p>
    <p class="fact right">If you kiss your kids only once each day, that's 1,460 kisses.</p>
    <p class="fact left">If you have client meetings four times a month, you'll meet with 36 clients.</p>
    <p class="fact right">If you kiss your kids only once each day, that's 1,460 kisses.</p>
    <p class="fact left">If you have client meetings four times a month, you'll meet with 36 clients.</p>
    <p class="fact right">If you kiss your kids only once each day, that's 1,460 kisses.</p>
    <p class="fact left">If you have client meetings four times a month, you'll meet with 36 clients.</p>
    <p class="fact right">If you kiss your kids only once each day, that's 1,460 kisses.</p>
  </section>
</body>
</html>
```